Design a sleek menu for our new smoothie and snacks shop”Glee”

requiring a store drinks and snacks menu we would like to have a white background for the menu . I would like to have fruit watermarks like in our original design concept , For reference ,please refer to the pictures . The font and layout of the menu should be modern , simple but stylish and reflect a smoothie shop.
we will be proving the menu contents to input once we agree to the design concept .
here are the menu documents

smoothies

Regular 16oz £4.99 Large 20oz £5.99
substitute semi skim for any dairy free milks for .50p
add vegan protein or regular protein for .50p

Berry set go
mixed berries, banana, coconut yogurt, milk

Green Machine
Spinach, avocado, matcha, banana, milk, agave

Power to the purple
Blueberries, banana, açai, coconut milk

Mango Monsoon
Mango, apple, strawberry, coconut milk, vanilla yogurt, agave

Go Ape Glee
Oats, banana, cinnamon, dates, almond butter

Caribbean Dream
Pineapple, spinach, banana, coconut milk

Mocha lotta
Oats, banana, cinnamon, cocoa, espresso, skim milk

Cocoa Banana
Oats, banana, cocoa, cinnamon, peanut butter , agave
*almond butter substitute is available

PB & J Day
Frozen berries, banana, peanut butter, maple syrup, coconut milk
*Spinach is optional

Strawberry Glee
Strawberries, banana, coconut milk, orange juice, agave

Kale Krush
Spinach, kale, pineapple, apple juice

Young Blood
Celery, lemon, apple

Berry Beautiful
Blueberries, banana, vanilla yogurt, soy milk, collagen protein, agave,

Shakes
Large 16oz £6
Add Protein for .50p

Avo Shake
Avocado, banana, skim milk, vanilla

Cocoa Shake
Avocado, cocoa powder, coconut milk, banana, maple syrup
*can substitute avocado with dairy free ice cream

Sweet Vegan
Dairy free vanilla Ice cream, banana, cocoa powder, coconut milk, agave

The last straw
Strawberry ,dates , dairy free ice cream, coconut milk, agave
*substitute dairy free ice cream for avocado

Caffeine frenzy
Espresso, banana, dairy free ice cream, cocoa powder, almond milk, agave

Berry Bunch
Oats, mixed berries, banana, dates ,soy milk, dairy free ice cream

Immune boosters
Regular 16 oz £6
Smoothie Bowl £5.50 * Available on a seasonal basis

The yellow one: Pineapple turmeric
Pineapple, banana, lemon, agave, ginger,tumeric,coconut water

The Red one : Citrus Berry Ginger
Orange, strawberry, lemon, ginger , almond milk

The Orange one : Citrus carrot
Grapefruit, clementine, carrot,mango,yogurt,lemon,tumeric

Teas
Regular £2
Green geisha
Breakfast blend
Lemon & ginger
Moroccan mint

Iced Frappucino
* Substitute for non dairy for .50p
Regular £3.50
Cappuccino - expresso, milk, ice
Mocha- cocoa ,milk, ice
Strawberry's n cream- Strawberry,cream,ice
Mighty Matcha - Matcha, cream, ice
Vanilla Bean- Vanilla, cream, ice
Glee Sandwiches
£4.50

Avocado
Avocado , mozerella,tomatoe, pesto

Spicy Tuna
Tuna, Chilli peppers, mayo, salt, pepper

Tunacado
Tuna, avocado, mayo, salt, pepper

BLT
Turkey Rasher, lettuce, mayo, tomatoe

American Grilled Cheese
Mature Cheddar , wholewheat bread
*sourdough bread is optional

Yogurt
£3
Coconut ,Vanilla yogurt , banana, granola

Bowls
£4.50
+ protein=.50p

Acai Bowl
Acai, Raspberry,blueberry,banana,almond milk, granola
*Topping: granola and ½ banana sliced ,chia seeds

Cocoa Bowl
Cocoa,banana,peanut butter,almond milk
Toppings : chocolate granola, peanut butter ,chia seeds,1/2 banana sliced

Target Market(s)

any age , predominately ages 20+

Industry/Entity Type

food & drink

Colors

Designer to choose colors to be used in the design.

Requirements
Must have
• clean, modern concept
Nice to have
• white background, fruits in the background -animated or actual ones
Should not have
• no dark background concepts

```html
<!DOCTYPE html>
<html lang="en">
<head>
<meta charset="utf-8">
<title>Glee Menu</title>
<link href="https://fonts.googleapis.com/css2?family=Quicksand:wght@500;600&family=Nunito+Sans:wght@400;600&display=swap" rel="stylesheet">
<style>
  :root{
    --paper:#ffffff;
    --panel:#b8f970;
    --band:#86f52c;
    --ink:#1a1d24;
    --accent:#ff1f6b;
    --navy:#1d2238;
    --sketch:#d9dde0;
    --heading-shadow:#5c6b4c;
  }
  *{margin:0;padding:0;box-sizing:border-box}
  html,body{width:880px;height:1200px;overflow:hidden;background:var(--paper)}
  .menu{position:relative;width:880px;height:1200px;background:var(--paper);
    font-family:"Nunito Sans",Arial,sans-serif;color:var(--ink)}
  .fruit{position:absolute;background:var(--sketch);border-radius:50%;opacity:.75}
  .panel{position:absolute;left:28px;top:26px;width:822px;height:1146px;background:var(--panel)}
  .watermark{position:absolute;border-radius:50%;background:rgba(255,255,255,.12)}
  .brand-tab{position:absolute;left:376px;top:0;width:128px;height:112px;background:var(--navy);
    display:flex;align-items:center;justify-content:center;gap:6px}
  .brand-tab .brand-name{font-family:"Quicksand",sans-serif;font-weight:600;font-size:30px;color:#fff}
  .brand-tab .brand-dot{width:8px;height:8px;border-radius:50%;background:var(--accent)}
  .section-title{position:absolute;font-family:"Quicksand",sans-serif;font-weight:500;font-size:27px;
    color:#fff;text-shadow:1px 1px 0 var(--heading-shadow),2px 2px 2px rgba(0,0,0,.25);letter-spacing:.2px;line-height:1}
  .right{text-align:right}
  .band{position:absolute;background:var(--band);font-size:13px;line-height:13px}
  .price{color:var(--accent);font-family:"Quicksand",sans-serif;font-weight:600}
  .item{position:absolute;font-size:13px;line-height:11.8px}
  .item-name{font-weight:600;font-size:14px;line-height:13px;text-transform:uppercase}
  .note{color:var(--accent)}
  .divider{position:absolute;height:0;border-top:1.5px dashed var(--ink)}
  .col-rule{position:absolute;left:440px;top:160px;height:970px;border-left:1.5px dashed var(--ink)}
  .list-line{position:absolute;font-size:13.5px;font-weight:600;text-transform:uppercase;line-height:14px}
  .list-line span{font-weight:400;text-transform:none}
</style>
</head>
<body>
<div class="menu">
  <div class="fruit" role="img" aria-label="Sketched apple halves" style="left:-20px;top:10px;width:90px;height:120px"></div>
  <div class="fruit" role="img" aria-label="Sketched strawberry and banana" style="left:500px;top:-10px;width:140px;height:80px"></div>
  <div class="fruit" role="img" aria-label="Sketched grapes" style="left:840px;top:350px;width:60px;height:420px;border-radius:30px"></div>
  <div class="fruit" role="img" aria-label="Sketched cherries and kiwi" style="left:-20px;top:260px;width:50px;height:300px;border-radius:25px"></div>
  <div class="fruit" role="img" aria-label="Sketched apple" style="left:830px;top:730px;width:70px;height:90px"></div>
  <div class="fruit" role="img" aria-label="Sketched fruit border" style="left:-10px;top:1140px;width:900px;height:90px;border-radius:40px"></div>

  <div class="panel">
    <div class="watermark" role="img" aria-label="Faint fruit watermark" style="left:360px;top:380px;width:170px;height:170px"></div>
    <div class="watermark" role="img" aria-label="Faint fruit watermark" style="left:260px;top:640px;width:150px;height:150px"></div>
    <div class="watermark" role="img" aria-label="Faint fruit watermark" style="left:440px;top:1060px;width:120px;height:120px"></div>
  </div>

  <div class="brand-tab"><span class="brand-name">Glee</span><span class="brand-dot"></span></div>

  <div class="col-rule"></div>

  <!-- Smoothies -->
  <h2 class="section-title" style="left:74px;top:79px">SMOOTHIES</h2>
  <div class="band" style="left:0;top:112px;width:418px;height:46px;padding:2px 0 0 74px">
    <div class="price">REGULAR 16OZ £4.99 LARGE 20OZ £5.99</div>
    <div>Substitute semi skim for any dairy free milks for .50p</div>
    <div>add vegan protein or regular protein for .50p</div>
  </div>

  <div class="item" style="left:74px;top:179px"><div class="item-name">Berry Set Go</div>mixed berries, banana, coconut yogurt, milk</div>
  <div class="item" style="left:74px;top:214px"><div class="item-name">Green Machine</div>Spinach, avocado, matcha, banana, milk, agave</div>
  <div class="item" style="left:74px;top:250px"><div class="item-name">Power to the Purple</div>Blueberries, banana, açai, coconut milk</div>
  <div class="item" style="left:74px;top:284px"><div class="item-name">Mango Monsoon</div>Mango, apple, strawberry, coconut milk,<br>vanilla yogurt, agave</div>
  <div class="item" style="left:74px;top:330px"><div class="item-name">Go Ape Glee</div>Oats, banana, cinnamon, dates, almond butter</div>
  <div class="item" style="left:74px;top:366px"><div class="item-name">Caribbean Dream</div>Pineapple, spinach, banana, coconut milk</div>
  <div class="item" style="left:74px;top:401px"><div class="item-name">Mocha Lotta</div>Oats, banana, cinnamon, cocoa,<br>espresso, skim milk</div>
  <div class="item" style="left:74px;top:447px"><div class="item-name">Cocoa Banana</div>Oats, banana, cocoa, cinnamon,<br>peanut butter, agave<br><span class="note">*almond butter substitute is available</span></div>
  <div class="item" style="left:74px;top:506px"><div class="item-name">PB &amp; J Day</div>Frozen berries, banana, peanut butter,<br>maple syrup, coconut milk<br>*Spinach is optional</div>
  <div class="item" style="left:74px;top:564px"><div class="item-name">Strawberry Glee</div>Strawberries, banana, coconut milk,<br>orange juice, agave</div>
  <div class="item" style="left:74px;top:610px"><div class="item-name">Kale Krush</div>Spinach, kale, pineapple, apple juice</div>
  <div class="item" style="left:74px;top:646px"><div class="item-name">Young Blood</div>Celery, lemon, apple</div>
  <div class="item" style="left:74px;top:681px"><div class="item-name">Berry Beautiful</div>Blueberries, banana, vanilla yogurt, soy milk,<br>collagen protein, agave,</div>

  <div class="divider" style="left:80px;top:732px;width:312px"></div>

  <!-- Shakes -->
  <h2 class="section-title" style="left:72px;top:745px">SHAKES</h2>
  <div class="band" style="left:0;top:776px;width:228px;height:48px;padding:8px 0 0 77px">
    <div class="price">LARGE 16OZ £6</div>
    <div>Add Protein for .50p</div>
  </div>

  <div class="item" style="left:71px;top:829px"><div class="item-name">Avo Shake</div>Avocado, banana, skim milk, vanilla</div>
  <div class="item" style="left:71px;top:864px"><div class="item-name">Cocoa Shake</div>Avocado, cocoa powder, coconut milk,<br>banana, maple syrup<br><span class="note">*can substitute avocado with dairy<br>free ice cream</span></div>
  <div class="item" style="left:71px;top:934px"><div class="item-name">Sweet Vegan</div>Dairy free vanilla Ice cream, banana,<br>cocoa powder, coconut milk, agave</div>
  <div class="item" style="left:71px;top:981px"><div class="item-name">The Last Straw</div>Strawberry ,dates , dairy free ice cream,<br>coconut milk, agave<br><span class="note">*avocado can be substituted with avocado</span></div>
  <div class="item" style="left:71px;top:1039px"><div class="item-name">Caffeine Frenzy</div>Espresso, banana, dairy free ice cream,<br>cocoa powder, almond milk, agave</div>
  <div class="item" style="left:71px;top:1086px"><div class="item-name">Berry Bunch</div>Oats, mixed berries, banana, dates ,soy milk,<br>dairy free ice cream</div>

  <!-- Immune boosters -->
  <h2 class="section-title right" style="right:72px;top:79px">IMMUNE BOOSTERS</h2>
  <div class="band right" style="left:468px;top:112px;width:412px;height:46px;padding:3px 80px 0 0">
    <div class="price">REGULAR 16 OZ £6</div>
    <div class="price">SMOOTHIE BOWL £5.50</div>
    <div>Available on a seasonal basis</div>
  </div>
  <div class="item right" style="right:71px;top:164px"><div class="item-name">The Yellow One: Pineapple turmeric</div>Pineapple, banana, lemon, agave, ginger,<br>tumeric,coconut water</div>
  <div class="item right" style="right:71px;top:210px"><div class="item-name">The Red One : Citrus Berry Ginger</div>Orange, strawberry, lemon, ginger ,<br>almond milk</div>
  <div class="item right" style="right:71px;top:257px"><div class="item-name">The Orange One : Citrus carrot</div>Grapefruit, clementine, carrot,mango,<br>yogurt,lemon,tumeric</div>

  <div class="divider" style="left:476px;top:306px;width:308px"></div>

  <!-- Teas -->
  <h2 class="section-title right" style="right:72px;top:315px">TEAS</h2>
  <div class="band" style="left:666px;top:346px;width:214px;height:22px;padding:4px 0 0 48px"><span class="price">REGULAR £2</span></div>
  <div class="list-line right" style="right:74px;top:374px">Green Geisha</div>
  <div class="list-line right" style="right:74px;top:394px">Breakfast Blend</div>
  <div class="list-line right" style="right:74px;top:414px">Lemon &amp; Ginger</div>
  <div class="list-line right" style="right:74px;top:434px">Moroccan Mint</div>

  <div class="divider" style="left:476px;top:458px;width:308px"></div>

  <!-- Iced frappucino -->
  <h2 class="section-title right" style="right:72px;top:465px">ICED FRAPPUCINO</h2>
  <div class="band" style="left:666px;top:494px;width:214px;height:22px;padding:4px 0 0 47px"><span class="price">REGULAR £4</span></div>
  <div class="list-line right" style="right:74px;top:522px">Cappuccino <span>- expresso, cream, ice</span></div>
  <div class="list-line right" style="right:74px;top:542px">Cocoa Hazelnut <span>- hazelnut cocoa ,cream, ice</span></div>
  <div class="list-line right" style="right:74px;top:562px">Strawberry's N Cream<span>- Strawberry,cream,ice</span></div>
  <div class="list-line right" style="right:74px;top:582px">Mighty Matcha <span>- Matcha, cream, ice</span></div>

  <div class="divider" style="left:476px;top:608px;width:308px"></div>

  <!-- Sandwiches -->
  <h2 class="section-title right" style="right:72px;top:617px">GLEE SANDWICHES</h2>
  <div class="band" style="left:666px;top:646px;width:214px;height:23px;padding:4px 0 0 89px"><span class="price">£4.50</span></div>
  <div class="item right" style="right:70px;top:680px"><div class="item-name">Avocado</div>Avocado , mozerella,tomatoe, pesto</div>
  <div class="item right" style="right:70px;top:715px"><div class="item-name">Spicy Tuna</div>Tuna, Chilli peppers, mayo, salt, pepper</div>
  <div class="item right" style="right:70px;top:750px"><div class="item-name">Tunacado</div>Tuna, avocado, mayo, salt, pepper</div>
  <div class="item right" style="right:70px;top:786px"><div class="item-name">BLT</div>Turkey Rasher, lettuce, mayo, tomatoe</div>
  <div class="item right" style="right:70px;top:821px"><div class="item-name">American Grilled Cheese</div>Mature Cheddar , wholewheat bread<br><span class="note">*sourdough bread is optional</span></div>

  <div class="divider" style="left:476px;top:870px;width:308px"></div>

  <!-- Yogurt -->
  <h2 class="section-title right" style="right:72px;top:875px">YOGURT</h2>
  <div class="band" style="left:666px;top:904px;width:214px;height:22px;padding:4px 0 0 102px"><span class="price">£3</span></div>
  <div class="list-line" style="left:463px;top:934px">Coconut, Vanilla Yogurt, Banana, Granola</div>

  <div class="divider" style="left:476px;top:957px;width:308px"></div>

  <!-- Bowls -->
  <h2 class="section-title right" style="right:72px;top:966px">BOWLS</h2>
  <div class="band" style="left:593px;top:995px;width:287px;height:23px;padding:4px 0 0 87px"><span class="price">£4.50 + PROTEIN=.50P</span></div>
  <div class="item right" style="right:70px;top:1027px"><div class="item-name">Acai Bowl</div>Acai, Raspberry,blueberry,banana,almond milk,<br>granola<br><span class="note" style="line-height:16px">*Topping: granola and ½ banana sliced ,chia seeds</span></div>
  <div class="item right" style="right:70px;top:1085px"><div class="item-name">Cocoa Bowl</div>Cocoa,banana,peanut butter,almond milk<br><span class="note">*almond butter substitute is available</span><br>Toppings : chocolate granola, peanut butter ,chia<br>seeds,1/2 banana sliced</div>
</div>
</body>
</html>
```